Business Broker Graphics Package

Hi,

Seeking a smart and professional graphics package design including business card design (double-sided) and letterhead and PowerPoint slide template.

3 Deliverables:

1. Company Letterhead
2. Business Card (two sided) (will consider one sided designs)
3. PowerPoint Template. Requires cover PPT and 2nd page design.

For the prototype use this info:
Marcus Dellorane RPA
Registered Practice Adviser
5678 Harlow Rd.
Larkmoor, KS 60213
555.014.2273
Demo@Quillbrookpath.com
www.QuillbrookPath.com

I'll give exact information to winner to finalize later.

I've attached the logo..

Business card will be double sided and info for back of card is in attachment.

Look forward to your great ideas and concepts!

Target Market(s)

President's and business owners, CPA's and other professionals.

Industry/Entity Type

Business

Requirements
Nice to have
• Prefer horizontal card, but will consider vertical card design.

The business card should be all or primarily white. Text colors should be same as logo creative combination of black and forest green.

PowerPoint can be white background or lighter palette of colors I like gold color. I do not like darkly colored PowerPoint designs I prefer light and bright designs.

```html
<!DOCTYPE html>
<html lang="en">
<head>
<meta charset="utf-8">
<title>Quillbrook Path Stationery Set</title>
<link rel="stylesheet" href="https://fonts.googleapis.com/css2?family=Roboto:wght@400;500&family=Source+Sans+3:wght@400;600;700&display=swap">
<style>
  :root {
    --canvas: #adadad;
    --paper: #ffffff;
    --ink: #1e1e1e;
    --ink-soft: #555555;
    --charcoal: #242122;
    --band-grey: #3b3b3b;
    --forest: #0b3d23;
    --rule: #c9c9c9;
    --on-dark: #e8e8e8;
    --on-dark-soft: #bdbdbd;
  }
  * { box-sizing: border-box; margin: 0; padding: 0; }
  html, body { width: 1200px; height: 640px; overflow: hidden; }
  body { background: var(--canvas); position: relative; font-family: "Source Sans 3", Arial, sans-serif; color: var(--ink); }
  .sheet { position: absolute; background: var(--paper); box-shadow: 0 1px 3px rgba(0,0,0,.25); overflow: hidden; }
  .sheet--dark { background: var(--charcoal); }

  .wordmark { position: absolute; display: flex; flex-direction: column; align-items: flex-start; }
  .wordmark__name { display: flex; align-items: center; gap: 4px; font-family: "Roboto", Arial, sans-serif; font-weight: 500; color: var(--ink); letter-spacing: .02em; white-space: nowrap; }
  .wordmark__dot { display: inline-block; background: var(--forest); }
  .wordmark__tag { font-family: "Source Sans 3", Arial, sans-serif; font-weight: 700; color: var(--ink); white-space: nowrap; letter-spacing: .01em; }

  .person { position: absolute; font-family: "Roboto", Arial, sans-serif; white-space: nowrap; }
  .person__name { font-weight: 500; color: var(--ink); }
  .person__title { color: var(--ink-soft); }
  .sheet--dark .person__name { color: #f2f2f2; }
  .sheet--dark .person__title { color: var(--on-dark-soft); }

  .contacts { position: absolute; list-style: none; font-family: "Roboto", Arial, sans-serif; color: var(--ink); white-space: nowrap; }
  .contacts li { display: flex; align-items: center; gap: 4px; }
  .contacts svg { fill: currentColor; flex: none; }
  .sheet--dark .contacts { color: var(--on-dark); }

  .rule-h { position: absolute; height: 1px; background: var(--rule); }
  .rule-v { position: absolute; width: 1px; background: var(--rule); }

  .footer-band { position: absolute; left: 0; bottom: 0; }

  .letterhead { left: 37px; top: 22px; width: 450px; height: 584px; }
  .letter { position: absolute; left: 41px; top: 100px; width: 376px; font-size: 7.4px; line-height: 13.3px; color: #111; }
  .letter__strong { font-weight: 700; }
  .letter__intro { margin-bottom: 24px; }
  .letter p.letter__para { margin-bottom: 13.3px; }
  .letter__signature { display: block; width: 150px; height: 32px; margin: 2px 0 6px; background: linear-gradient(90deg, #d6d6d6, #f2f2f2); }

  .solutions { position: absolute; font-family: "Roboto", Arial, sans-serif; color: var(--on-dark); }
  .solutions__title { font-weight: 500; color: #f5f5f5; letter-spacing: .01em; }
  .solutions__list { list-style: none; display: flex; color: var(--on-dark-soft); }
  .solutions__list li::before { content: ""; display: inline-block; width: 4px; height: 4px; background: #f0f0f0; margin-right: 3px; vertical-align: 1px; }
  .solutions--row { left: 0; right: 0; text-align: center; }
  .solutions--row .solutions__list { justify-content: center; gap: 5px; font-size: 6.5px; margin-top: 6px; }
  .solutions--row .solutions__title { font-size: 7.6px; }
  .solutions--stack .solutions__title { font-size: 7.8px; }
  .solutions--stack .solutions__list { flex-direction: column; gap: 7px; font-size: 6.6px; margin-top: 8px; }

  .dark-strip { position: absolute; left: 0; right: 0; bottom: 0; background: var(--charcoal); }
</style>
</head>
<body>

<svg width="0" height="0" style="position:absolute" aria-hidden="true">
  <defs>
    <symbol id="icon-phone" viewBox="0 0 10 10"><rect x="2.5" y="0.5" width="5" height="9" rx="1"/><rect x="3.3" y="1.5" width="3.4" height="5.5" fill="#fff"/></symbol>
    <symbol id="icon-mail" viewBox="0 0 10 10"><rect x="0.5" y="2" width="9" height="6.5"/><path d="M1 2.6 5 5.6 9 2.6" fill="none" stroke="#fff" stroke-width="0.9"/></symbol>
    <symbol id="icon-web" viewBox="0 0 10 10"><circle cx="5" cy="5" r="4.5"/><path d="M0.7 5h8.6M5 0.7v8.6M2 2.6c2 1 4 1 6 0M2 7.4c2-1 4-1 6 0" fill="none" stroke="#fff" stroke-width="0.7"/></symbol>
    <symbol id="icon-pin" viewBox="0 0 10 10"><path d="M5 0.4a3.4 3.4 0 0 0-3.4 3.4C1.6 6.4 5 9.6 5 9.6s3.4-3.2 3.4-5.8A3.4 3.4 0 0 0 5 0.4z"/><circle cx="5" cy="3.8" r="1.2" fill="#fff"/></symbol>
  </defs>
</svg>

<!-- Letterhead -->
<section class="sheet letterhead" aria-label="Letterhead">
  <div class="wordmark" style="left:35px;top:44px;">
    <span class="wordmark__name" style="font-size:17px;"><span class="wordmark__dot" style="width:7px;height:7px;"></span>Quillbrook Path</span>
    <span class="wordmark__tag" style="font-size:6.2px;margin-top:2px;">Sale Purchase Expansion Advisers</span>
  </div>
  <div class="person" style="right:116px;top:53px;text-align:right;">
    <div class="person__name" style="font-size:8px;">Marcus Dellorane RPA</div>
    <div class="person__title" style="font-size:5px;">Registered Practice Adviser</div>
  </div>
  <div class="rule-v" style="left:340px;top:38px;height:36px;"></div>
  <ul class="contacts" style="left:345px;top:38px;font-size:5.6px;line-height:9px;">
    <li><svg width="6" height="6"><use href="#icon-phone"/></svg>555.014.2273</li>
    <li><svg width="6" height="6"><use href="#icon-mail"/></svg>Demo@Quillbrookpath.com</li>
    <li><svg width="6" height="6"><use href="#icon-web"/></svg>www.QuillbrookPath.com</li>
    <li><svg width="6" height="6"><use href="#icon-pin"/></svg>5678 Harlow Rd. Larkmoor, KS 60213</li>
  </ul>

  <div class="letter">
    <div>To</div>
    <div class="letter__strong">The Lorem Ipsum</div>
    <div class="letter__intro">Sample text for printing and typesetting industry</div>
    <p class="letter__para">Lorem Ipsum is simply dummy text of the printing and typesetting industry. Lorem Ipsum has been the industry's standard dummy text ever since the 1500s, when an unknown printer took a galley of type and scrambled it to make a type specimen book. It has survived not only five centuries, but also the leap into electronic typesetting, remaining essentially unchanged. It was popularised in the 1960s with the release of Letraset sheets containing Lorem Ipsum passages, and more recently with desktop publishing software like Aldus PageMaker including versions of Lorem Ipsum.</p>
    <p class="letter__para">It is a long established fact that a reader will be distracted by the readable content of a page when looking at its layout. The point of using Lorem Ipsum is that it has a more-or-less normal distribution of letters, as opposed to using 'Content here, content here', making it look like readable English. Many desktop publishing packages and web page editors now use Lorem Ipsum as their default model text, and a search for 'lorem ipsum' will uncover many web sites still in their infancy. Various versions have evolved over the years, sometimes by accident, sometimes on purpose (injected humour and the It is a long established fact that a reader will be distracted by the readable content of a page when looking at its layout. The point of using Lorem Ipsum is that it has a more-or-less normal distribution of letters, as opposed to using 'Content here, content here', making it look like readable English. Many desktop publishing packages and web page editors now use Lorem Ipsum as their default model text, and a search for 'lorem ipsum' will uncover many web sites still in their infancy.</p>
    <p class="letter__para">It is a long established fact that a reader will be distracted by the readable content of a page when looking at its layout. The point of using Lorem Ipsum is that it has a more-or-less normal distribution of letters, as opposed to using 'Content here, content here', making it look like readable English. Many desktop publishing packages and web page editors now use Lorem Ipsum as their default model text, and a search for 'lorem ipsum' will uncover many web sites still in their infancy. Various versions have evolved over the years, sometimes by accident, sometimes on purpose.</p>
    <span class="letter__signature" role="img" aria-label="Handwritten signature of the sender"></span>
    <div class="letter__strong">The Lorem Ipsum</div>
    <div>Sample text for printing and typesetting industry</div>
  </div>

  <svg class="footer-band" width="450" height="19" viewBox="0 0 450 19" aria-hidden="true">
    <rect x="0" y="9" width="276" height="10" fill="var(--band-grey)"/>
    <path d="M270 19 L275 4 Q277 0 282 0 L450 0 L450 19 Z" fill="var(--forest)"/>
  </svg>
</section>

<!-- Card front, white -->
<section class="sheet" style="left:517px;top:22px;width:264px;height:155px;" aria-label="Business card front">
  <div class="wordmark" style="left:19px;top:46px;">
    <span class="wordmark__name" style="font-size:12.5px;"><span class="wordmark__dot" style="width:5px;height:5px;"></span>Quillbrook Path</span>
    <span class="wordmark__tag" style="font-size:5px;margin-top:1px;">Sale Purchase Expansion Advisers</span>
  </div>
  <div class="person" style="right:19px;top:63px;text-align:right;">
    <div class="person__name" style="font-size:10.3px;">Marcus Dellorane RPA</div>
    <div class="person__title" style="font-size:6.3px;margin-top:2px;">Registered Practice Adviser</div>
  </div>
  <div class="rule-h" style="left:19px;top:82px;width:124px;"></div>
  <ul class="contacts" style="left:19px;top:88px;font-size:6.6px;line-height:9.3px;">
    <li><svg width="6" height="6"><use href="#icon-phone"/></svg>555.014.2273</li>
    <li><svg width="6" height="6"><use href="#icon-mail"/></svg>Demo@Quillbrookpath.com</li>
    <li><svg width="6" height="6"><use href="#icon-web"/></svg>www.QuillbrookPath.com</li>
    <li><svg width="6" height="6"><use href="#icon-pin"/></svg>5678 Harlow Rd. Larkmoor, KS 60213</li>
  </ul>
  <svg class="footer-band" width="264" height="13" viewBox="0 0 264 13" aria-hidden="true">
    <rect x="0" y="6" width="160" height="7" fill="var(--band-grey)"/>
    <path d="M157 13 L160 3 Q161 0 165 0 L264 0 L264 13 Z" fill="var(--forest)"/>
  </svg>
</section>

<!-- Card back, white with dark strip -->
<section class="sheet" style="left:809px;top:22px;width:264px;height:155px;" aria-label="Business card back">
  <div class="wordmark" style="left:0;right:0;top:34px;align-items:center;">
    <span class="wordmark__name" style="font-size:22px;"><span class="wordmark__dot" style="width:8px;height:8px;"></span>Quillbrook Path</span>
    <span class="wordmark__tag" style="font-size:8.4px;margin-top:2px;">Sale Purchase Expansion Advisers</span>
  </div>
  <div class="dark-strip" style="height:54px;">
    <div class="solutions solutions--row" style="top:14px;">
      <div class="solutions__title">OWNERSHIP SOLUTIONS</div>
      <ul class="solutions__list"><li>Business Sale</li><li>Acquisition</li><li>Exit Planning</li><li>Valuation</li><li>Growth Engineering</li></ul>
    </div>
  </div>
</section>

<!-- Card front, dark -->
<section class="sheet sheet--dark" style="left:517px;top:187px;width:264px;height:155px;" aria-label="Business card front, dark version">
  <div class="person" style="right:19px;top:52px;text-align:right;">
    <div class="person__name" style="font-size:10.3px;">Marcus Dellorane RPA</div>
    <div class="person__title" style="font-size:6.3px;margin-top:2px;">Registered Practice Adviser</div>
  </div>
  <div class="rule-h" style="left:19px;top:71px;width:124px;background:#4a4a4a;"></div>
  <ul class="contacts" style="left:19px;top:78px;font-size:6.6px;line-height:9.3px;">
    <li><svg width="6" height="6"><use href="#icon-phone"/></svg>555.014.2273</li>
    <li><svg width="6" height="6"><use href="#icon-mail"/></svg>Demo@Quillbrookpath.com</li>
    <li><svg width="6" height="6"><use href="#icon-web"/></svg>www.QuillbrookPath.com</li>
    <li><svg width="6" height="6"><use href="#icon-pin"/></svg>5678 Harlow Rd. Larkmoor, KS 60213</li>
  </ul>
</section>

<!-- Card back, dark -->
<section class="sheet sheet--dark" style="left:809px;top:187px;width:264px;height:155px;" aria-label="Business card back, dark version">
  <div class="solutions solutions--stack" style="left:24px;top:34px;">
    <div class="solutions__title">OWNERSHIP SOLUTIONS</div>
    <ul class="solutions__list"><li>Business Sale</li><li>Acquisition</li><li>Exit Planning</li><li>Valuation</li><li>Growth Engineering</li></ul>
  </div>
</section>

<!-- Card single-sided -->
<section class="sheet" style="left:517px;top:355px;width:264px;height:155px;" aria-label="Single-sided business card">
  <div class="wordmark" style="left:19px;top:33px;">
    <span class="wordmark__name" style="font-size:12.5px;"><span class="wordmark__dot" style="width:5px;height:5px;"></span>Quillbrook Path</span>
    <span class="wordmark__tag" style="font-size:5px;margin-top:1px;">Sale Purchase Expansion Advisers</span>
  </div>
  <div class="person" style="right:19px;top:50px;text-align:right;">
    <div class="person__name" style="font-size:10.3px;">Marcus Dellorane RPA</div>
    <div class="person__title" style="font-size:6.3px;margin-top:2px;">Registered Practice Adviser</div>
  </div>
  <div class="rule-h" style="left:19px;top:69px;width:124px;"></div>
  <ul class="contacts" style="left:19px;top:75px;font-size:6.6px;line-height:9.3px;">
    <li><svg width="6" height="6"><use href="#icon-phone"/></svg>555.014.2273</li>
    <li><svg width="6" height="6"><use href="#icon-mail"/></svg>Demo@Quillbrookpath.com</li>
    <li><svg width="6" height="6"><use href="#icon-web"/></svg>www.QuillbrookPath.com</li>
    <li><svg width="6" height="6"><use href="#icon-pin"/></svg>5678 Harlow Rd. Larkmoor, KS 60213</li>
  </ul>
  <div class="dark-strip" style="height:40px;">
    <div class="solutions solutions--row" style="top:10px;">
      <div class="solutions__title">OWNERSHIP SOLUTIONS</div>
      <ul class="solutions__list" style="margin-top:4px;"><li>Business Sale</li><li>Acquisition</li><li>Exit Planning</li><li>Valuation</li><li>Growth Engineering</li></ul>
    </div>
  </div>
</section>

<!-- Envelope -->
<section class="sheet" style="left:809px;top:355px;width:364px;height:253px;" aria-label="Envelope">
  <div class="wordmark" style="left:22px;top:24px;">
    <span class="wordmark__name" style="font-size:11px;"><span class="wordmark__dot" style="width:4px;height:4px;"></span>Quillbrook Path</span>
    <span class="wordmark__tag" style="font-size:4.4px;margin-top:1px;">Sale Purchase Expansion Advisers</span>
  </div>
  <div class="person" style="right:93px;top:16px;text-align:right;">
    <div class="person__name" style="font-size:6.2px;">Marcus Dellorane RPA</div>
    <div class="person__title" style="font-size:3.8px;">Registered Practice Adviser</div>
  </div>
  <div class="rule-v" style="left:275px;top:8px;height:32px;"></div>
  <ul class="contacts" style="left:279px;top:8px;font-size:4.6px;line-height:7.6px;">
    <li><svg width="5" height="5"><use href="#icon-phone"/></svg>555.014.2273</li>
    <li><svg width="5" height="5"><use href="#icon-mail"/></svg>Demo@Quillbrookpath.com</li>
    <li><svg width="5" height="5"><use href="#icon-web"/></svg>www.QuillbrookPath.com</li>
    <li><svg width="5" height="5"><use href="#icon-pin"/></svg>5678 Harlow Rd. Larkmoor, KS 60213</li>
  </ul>
  <svg class="footer-band" width="364" height="15" viewBox="0 0 364 15" aria-hidden="true">
    <rect x="0" y="7" width="214" height="8" fill="var(--band-grey)"/>
    <path d="M210 15 L214 3 Q215 0 219 0 L364 0 L364 15 Z" fill="var(--forest)"/>
  </svg>
</section>

</body>
</html>
```